Need help in designing new business card utilizing our new logo.

BuildMark Solutions works with Construction Business Owners, Managers & IT Professionals to strengthen software usage and increase user productivity.

Our Construction Accounting and Mobile Field Management Software Clients engage with us in the following areas:

New Software Implementations
Software Re-Implementations
Redesigning Software Usage at the User Level
Project Coordination & Management
Continued Software Support

Old tag line:
Weighing Options - Implementing Solutions

www.buildmark-solutions.example

Ridge 4 is a product, but not needed for a new business card.

```html
<!DOCTYPE html>
<html lang="en">
<head>
<meta charset="utf-8">
<title>BuildMark Solutions – Business Card</title>
<link href="https://fonts.googleapis.com/css2?family=Montserrat:wght@400;500;600;700&display=swap" rel="stylesheet">
<style>
  :root {
    --brand-blue: #27339b;
    --brand-blue-soft: #3440a6;
    --brand-gray: #c3c4c6;
    --text-gray: #5b5d62;
    --card-white: #ffffff;
    --backdrop: #e6e7ea;
  }
  * { box-sizing: border-box; margin: 0; padding: 0; }
  html, body { width: 1200px; height: 900px; overflow: hidden; }
  body {
    background: var(--backdrop);
    font-family: "Montserrat", sans-serif;
    display: flex;
    flex-direction: column;
    align-items: center;
    justify-content: center;
    gap: 36px;
  }
  .card {
    position: relative;
    width: 700px;
    height: 400px;
    overflow: hidden;
    box-shadow: 0 6px 20px rgba(0,0,0,0.18);
  }
  /* Front */
  .card-front { background: var(--card-white); }
  .wordmark {
    position: absolute;
    display: flex;
    align-items: center;
    gap: 12px;
    font-weight: 700;
    font-size: 26px;
    letter-spacing: 0.5px;
    white-space: nowrap;
  }
  .wordmark .mark-square { width: 22px; height: 22px; flex: none; }
  .card-front .wordmark { left: 48px; top: 44px; color: var(--brand-blue); }
  .card-front .wordmark .mark-square { background: var(--brand-blue); }
  .person { position: absolute; left: 48px; top: 112px; }
  .person-name { color: var(--brand-blue); font-weight: 700; font-size: 26px; }
  .person-title { color: var(--text-gray); font-size: 16px; margin-top: 2px; }
  .contact-list {
    position: absolute; left: 48px; top: 182px;
    list-style: none; color: var(--text-gray); font-size: 15px; line-height: 25px;
  }
  .contact-list li { display: flex; align-items: center; gap: 10px; white-space: nowrap; }
  .contact-list svg { width: 13px; height: 13px; fill: var(--brand-blue); flex: none; }
  .address { position: absolute; left: 48px; top: 290px; color: var(--text-gray); font-size: 15px; line-height: 24px; }
  .tagline {
    position: absolute; left: 226px; top: 342px;
    border-left: 2px solid var(--brand-blue);
    padding-left: 14px;
    color: var(--text-gray); font-size: 14px; line-height: 20px; font-weight: 500;
    white-space: nowrap;
  }
  .corner-bands { position: absolute; right: 0; bottom: 0; width: 290px; height: 270px; }
  /* Back */
  .card-back { background: var(--brand-blue); color: #fff; }
  .back-texture {
    position: absolute; left: 0; top: 0; width: 330px; height: 100%;
    background: linear-gradient(90deg, var(--brand-blue-soft) 0%, var(--brand-blue) 100%);
  }
  .card-back .wordmark { right: 60px; top: 70px; color: #fff; font-size: 34px; }
  .card-back .wordmark .mark-square { background: #fff; width: 26px; height: 26px; }
  .services {
    position: absolute; right: 60px; top: 170px;
    text-align: right; list-style: none; font-size: 17px; line-height: 30px; font-weight: 500;
    white-space: nowrap;
  }
</style>
</head>
<body>
  <section class="card card-front" aria-label="Business card front">
    <div class="wordmark"><span class="mark-square"></span>BuildMark Solutions</div>
    <div class="person">
      <p class="person-name">Dana R. Whitfield</p>
      <p class="person-title">Owner</p>
    </div>
    <ul class="contact-list">
      <li><svg viewBox="0 0 16 16"><path d="M3 1l3 3-1.5 2a9 9 0 0 0 5.5 5.5L12 10l3 3-2 2C6 15 1 10 1 3z"/></svg>800-555-0142 ext.100</li>
      <li><svg viewBox="0 0 16 16"><path d="M4 0h8a1 1 0 0 1 1 1v14a1 1 0 0 1-1 1H4a1 1 0 0 1-1-1V1a1 1 0 0 1 1-1zm1 2v10h6V2z"/></svg>518-555-0193</li>
      <li><svg viewBox="0 0 16 16"><path d="M0 3h16v10H0zm1.5 1.5L8 9l6.5-4.5V4h-13z"/></svg>dana.whitfield@buildmark-solutions.example</li>
      <li><svg viewBox="0 0 16 16"><circle cx="8" cy="8" r="7"/></svg>www.buildmark-solutions.example</li>
    </ul>
    <p class="address">14B Maple Avenue - PMB 118<br>Glenford NY 12400</p>
    <p class="tagline">Construction Accounting<br>Software Consultants</p>
    <svg class="corner-bands" viewBox="0 0 290 270" aria-hidden="true">
      <polygon points="290,0 290,60 90,270 30,270" fill="var(--brand-blue)"/>
      <polygon points="290,110 290,170 190,270 130,270" fill="var(--brand-gray)"/>
      <polygon points="290,210 290,270 230,270" fill="var(--brand-blue)"/>
    </svg>
  </section>

  <section class="card card-back" aria-label="Business card back">
    <div class="back-texture" role="img" aria-label="Faint decorative pattern area in light blue tones"></div>
    <div class="wordmark"><span class="mark-square"></span>BuildMark Solutions</div>
    <ul class="services">
      <li>New Software Implementations | Software Re-Implementations</li>
      <li>Redesigning Software Usage at the User Level</li>
      <li>Project Coordination &amp; Management</li>
      <li>Continued Software Support</li>
    </ul>
  </section>
</body>
</html>
```